Professional & attention grabbing.

A business card design, front and back. I already have a logo I will attach, but I am open to something new as well.
Things to include:
Name:
Title:
Phone:
Email:
Wanting something that is professional but attention grabbing.
Also we do a lot of work using drones on natural gas pipelines (leading the future)if you want to include any of that. I'm open to ideas.
Target Market(s)
Natural gas transmission industry / greenhouse gas mitigation industry
Industry/Entity Type
Business
Colors
Designer to choose colors to be used in the design.
Look and feel
Each slider illustrates characteristics of the customer's brand and the style your logo design should communicate.

```html
<!DOCTYPE html>
<html lang="en">
<head>
<meta charset="utf-8">
<title>Kestrel Line Inspections – Business Card</title>
<link href="https://fonts.googleapis.com/css2?family=Open+Sans:ital,wght@0,400;0,600;0,700;1,400&display=swap" rel="stylesheet">
<style>
  :root {
    --backdrop: #5a4a3d;
    --card: #ffffff;
    --ink: #333436;
    --brand-red: #c21f25;
    --panel-dark: #353634;
    --muted: #5d5e60;
    --pattern-grey: #e9e9e9;
    --pattern-pink: #f6e3e3;
  }
  * { margin: 0; padding: 0; box-sizing: border-box; }
  html, body {
    width: 1200px; height: 987px; overflow: hidden;
    background: var(--backdrop);
    font-family: "Open Sans", Arial, sans-serif;
  }
  .card {
    position: absolute; left: 293px; width: 615px; height: 352px;
    background: var(--card);
    box-shadow: 0 3px 8px rgba(0,0,0,.35);
    overflow: hidden;
  }
  .card--front { top: 130px; }
  .card--back { top: 505px; }

  .wordmark {
    position: absolute; left: 0; right: 0; top: 70px;
    display: flex; justify-content: center; align-items: center; gap: 14px;
  }
  .wordmark__square { width: 40px; height: 40px; background: var(--brand-red); }
  .wordmark__name {
    font-weight: 700; font-size: 30px; color: var(--ink);
    letter-spacing: .5px; text-transform: uppercase; line-height: 1;
  }

  .info-band {
    position: absolute; top: 211px; left: 0; right: 0; height: 109px;
    display: flex;
  }
  .identity {
    width: 306px; background: var(--brand-red); color: #fff;
    text-align: right; padding: 30px 30px 0 0;
  }
  .identity__name { font-weight: 600; font-size: 21px; line-height: 1.2; }
  .identity__title { font-size: 16px; line-height: 1.3; }
  .contacts {
    margin-left: 3px; flex: 1; background: var(--panel-dark); color: #fff;
    list-style: none; padding: 18px 0 0 30px; font-size: 15.5px;
  }
  .contacts li { display: flex; align-items: center; gap: 9px; height: 23.5px; }
  .contacts svg { width: 14px; height: 14px; fill: #fff; flex: none; }

  .back-pattern {
    position: absolute; inset: 0;
    background: linear-gradient(135deg, var(--pattern-grey), var(--pattern-pink) 50%, var(--pattern-grey));
  }
  .back-brand {
    position: absolute; left: 0; right: 0; top: 130px; text-align: center;
  }
  .back-brand__name {
    font-weight: 700; font-size: 34px; color: var(--ink);
    text-transform: uppercase; letter-spacing: .5px; line-height: 1.1;
  }
  .back-brand__web {
    margin-top: 14px; font-style: italic; font-size: 15px;
    letter-spacing: 3px; color: var(--muted);
  }
</style>
</head>
<body>
  <section class="card card--front">
    <div class="wordmark">
      <span class="wordmark__square"></span>
      <span class="wordmark__name">Kestrel Line Inspections</span>
    </div>
    <div class="info-band">
      <div class="identity">
        <p class="identity__name">JOHN SMITH</p>
        <p class="identity__title">CEO/Founder</p>
      </div>
      <ul class="contacts">
        <li>
          <svg viewBox="0 0 24 24" aria-hidden="true"><path d="M6.6 10.8a15.1 15.1 0 0 0 6.6 6.6l2.2-2.2a1 1 0 0 1 1-.25 11.4 11.4 0 0 0 3.6.57 1 1 0 0 1 1 1V20a1 1 0 0 1-1 1A17 17 0 0 1 3 4a1 1 0 0 1 1-1h3.5a1 1 0 0 1 1 1c0 1.25.2 2.45.57 3.57a1 1 0 0 1-.25 1z"/></svg>
          555 214 7730
        </li>
        <li>
          <svg viewBox="0 0 24 24" aria-hidden="true"><path d="M2 5h20v14H2zm2 2v.5l8 5 8-5V7zm0 2.8V17h16V9.8l-8 5z"/></svg>
          name@webname.com
        </li>
        <li>
          <svg viewBox="0 0 24 24" aria-hidden="true"><circle cx="12" cy="12" r="10"/><path d="M7 8c2 0 3 1 3 3s2 2 2 4-1 3-1 5M14 4c0 2 1 3 3 3s2 2 3 3" stroke="#353634" stroke-width="2" fill="none"/></svg>
          www.webname.com
        </li>
      </ul>
    </div>
  </section>

  <section class="card card--back">
    <div class="back-pattern" role="img" aria-label="Faint repeating pattern of the brand symbol in light grey and pale red tiles"></div>
    <div class="back-brand">
      <p class="back-brand__name">Kestrel Line<br>Inspections</p>
      <p class="back-brand__web">www.webname.com</p>
    </div>
  </section>
</body>
</html>
```